Home Security Company Business Card

Looking for a eye catching business card that is non traditional and stands out but yet still looks professional. It should include all the pertinent information such as name, title, address, telephone, e-mail, website address should definitely stand out and then finally the logo.

Target Market(s)

Residential and Commercial accounts mostly upscale accounts

Industry/Entity Type

Security

Contact Information for Business Card

Name
Title
Address
Office #
Cell #
E-mail
Website

Font styles to use
Serif
Sans Serif

Requirements
Must have
• Logo, two sided color configuration
Nice to have
• You decide
Should not have
• There really aren't any.

```html
<!DOCTYPE html>
<html lang="en">
<head>
<meta charset="utf-8">
<title>Keystone Security Systems – Business Card</title>
<link rel="stylesheet" href="https://fonts.googleapis.com/css2?family=Tinos:wght@400&display=swap">
<style>
  :root {
    --page-bg: #ecebe8;
    --card-bg: #ffffff;
    --card-edge: #f1f1f1;
    --brand-red: #9d1c21;
    --brand-gold: #d6a62a;
    --social-blue: #7aa6d6;
    --text-serif: "Tinos", "Times New Roman", serif;
  }
  * { box-sizing: border-box; margin: 0; padding: 0; }
  html, body { width: 1200px; height: 780px; overflow: hidden; }
  body {
    background: var(--page-bg);
    font-family: var(--text-serif);
    display: flex;
    align-items: center;
    justify-content: center;
    gap: 60px;
  }
  .card {
    position: relative;
    width: 520px;
    height: 300px;
    border-radius: 16px;
    background: linear-gradient(135deg, var(--card-bg) 0%, var(--card-bg) 55%, var(--card-edge) 100%);
    box-shadow: 0 2px 6px rgba(0,0,0,.18);
    overflow: hidden;
  }

  /* Shared name block: one colour, one weight, one line */
  .brand {
    display: flex;
    align-items: center;
    gap: 12px;
    color: var(--brand-red);
    font-weight: 400;
    white-space: nowrap;
  }
  .brand-dot {
    border-radius: 50%;
    background: var(--brand-gold);
    flex: none;
  }

  /* Front */
  .card-front .brand {
    position: absolute;
    left: 34px;
    top: 66px;
    font-size: 24px;
  }
  .card-front .brand-dot { width: 30px; height: 30px; }

  .social {
    position: absolute;
    right: 30px; top: 26px;
    display: flex; gap: 6px;
  }
  .social span {
    width: 20px; height: 20px; border-radius: 4px;
    background: var(--social-blue);
  }

  .holder {
    position: absolute;
    right: 32px; top: 112px;
    text-align: right;
    color: var(--brand-red);
  }
  .holder-name { font-size: 22px; line-height: 26px; }
  .holder-title { font-size: 12px; line-height: 14px; color: var(--brand-gold); }

  .divider {
    position: absolute;
    left: 34px; right: 30px; top: 160px;
    height: 1px;
    background: var(--brand-gold);
  }

  .contact {
    position: absolute;
    left: 34px; top: 186px;
    list-style: none;
    color: var(--brand-red);
    font-size: 13px;
    line-height: 22px;
  }
  .contact li { display: flex; align-items: center; gap: 8px; }
  .contact svg { width: 14px; height: 14px; flex: none; }

  .address {
    position: absolute;
    right: 32px; top: 186px;
    text-align: right;
    color: var(--brand-red);
    font-size: 13px;
    line-height: 22px;
    font-style: normal;
  }
  .address .web { color: var(--brand-gold); display: block; }

  /* Back */
  .card-back {
    display: flex;
    align-items: center;
    justify-content: center;
    background: linear-gradient(160deg, #fafafa 0%, #ededed 100%);
  }
  .card-back .brand { font-size: 28px; }
  .card-back .brand-dot { width: 34px; height: 34px; }
</style>
</head>
<body>

  <section class="card card-front" aria-label="Business card front">
    <div class="brand">
      <span class="brand-dot"></span>
      <span class="brand-name">Keystone Security Systems Inc.</span>
    </div>

    <div class="social" aria-label="Social profiles">
      <span></span><span></span><span></span>
    </div>

    <div class="holder">
      <div class="holder-name">Dale Hartwell</div>
      <div class="holder-title">Owner</div>
    </div>

    <div class="divider"></div>

    <ul class="contact">
      <li>
        <svg viewBox="0 0 14 14" aria-hidden="true"><rect width="14" height="14" rx="3" fill="#d6a62a"/><path d="M4 3.5c.5-.3 1-.2 1.3.3l.6 1.1c.2.4.1.8-.2 1l-.5.4c.4.9 1.1 1.6 2 2l.4-.5c.2-.3.6-.4 1-.2l1.1.6c.5.3.6.8.3 1.3-.4.7-1.2 1-2 .8C5.9 9.8 4.2 8.1 3.7 6c-.2-.8.1-1.6.3-2.5z" fill="#fff"/></svg>
        555-014-2290
      </li>
      <li>
        <svg viewBox="0 0 14 14" aria-hidden="true"><rect width="14" height="14" rx="3" fill="#d6a62a"/><rect x="4.5" y="2.5" width="5" height="9" rx="1" fill="#fff"/><rect x="5.3" y="3.5" width="3.4" height="6" fill="#d6a62a"/></svg>
        +1 555-014-2291
      </li>
      <li>
        <svg viewBox="0 0 14 14" aria-hidden="true"><rect width="14" height="14" rx="3" fill="#d6a62a"/><rect x="3" y="4" width="8" height="6" fill="#fff"/><path d="M3 4l4 3.2L11 4" stroke="#d6a62a" stroke-width=".9" fill="none"/></svg>
        info@keystonesecure.com
      </li>
    </ul>

    <address class="address">
      PO Box 418 Cedar Lane,<br>
      WA 98000 USA
      <span class="web">www.keystonesecure.com</span>
    </address>
  </section>

  <section class="card card-back" aria-label="Business card back">
    <div class="brand">
      <span class="brand-dot"></span>
      <span class="brand-name">Keystone Security Systems Inc.</span>
    </div>
  </section>

</body>
</html>
```